Social Media Graphics - Oakline Push REVISED

Create 6-7 individual social media graphics (square size) to encourage folks to join our online course called:

The Harvest Ledger Circle
How to Launch a Multi-Million Business From Scratch
Sign Up Today!

IMPORTANT: Make the largest and most prominent text on the graphic be: How to Launch a Multi-Million Business From Scratch

For the color scheme of the graphics, let's try a blue color palette; make sure the graphics appeal to both men and women

Make sure each graphic contains 1 of the 3 pics attached (crop pic as needed); and make sure one of the graphics is all TEXT only.

Target Market(s)

men and women looking to start a business

Industry/Entity Type

Entrepreneurship

Colors
0054AA
0677BA
7BADD7
CADEEF
E8F1F8

Requirements
Must have
• All the text and use the 3 pics provided; one graphic can be all text; Simple, modern design that's easy to read

```html
<!DOCTYPE html>
<html lang="en">
<head>
<meta charset="utf-8">
<title>The Harvest Ledger Circle – Sign Up</title>
<link rel="stylesheet" href="https://fonts.googleapis.com/css2?family=Anton&family=Oswald:wght@500;700&display=swap">
<style>
  :root {
    --ocean: #0473A1;
    --deep-teal: #083A4A;
    --midnight: #1F1D3B;
    --ring: #0673A0;
    --white: #FFFFFF;
    --portrait-light: #EEF3F7;
    --portrait-mid: #4A5F7A;
  }
  html, body {
    margin: 0;
    padding: 0;
    width: 1200px;
    height: 1200px;
    overflow: hidden;
    background: var(--midnight);
  }
  .social-card {
    display: block;
    width: 1200px;
    height: 1200px;
  }
  .bg-ocean { fill: var(--ocean); }
  .bg-midnight { fill: var(--midnight); }
  .bg-teal { fill: var(--deep-teal); }
  .frame-line { fill: none; stroke: var(--white); stroke-width: 2; }
  .portrait-ring { fill: var(--ring); }
  .course-pill { fill: var(--white); }
  .course-name {
    font-family: "Oswald", sans-serif;
    font-weight: 500;
    font-size: 80px;
    fill: var(--midnight);
  }
  .headline {
    font-family: "Anton", sans-serif;
    font-size: 92px;
    fill: var(--white);
  }
  .cta {
    font-family: "Oswald", sans-serif;
    font-weight: 700;
    font-size: 36px;
    fill: var(--white);
  }
</style>
</head>
<body>
<svg class="social-card" viewBox="0 0 1200 1200" xmlns="http://www.w3.org/2000/svg">
  <defs>
    <radialGradient id="portrait-fill" cx="50%" cy="35%" r="70%">
      <stop offset="0%" stop-color="#EEF3F7"/>
      <stop offset="55%" stop-color="#C9D3DD"/>
      <stop offset="100%" stop-color="#4A5F7A"/>
    </radialGradient>
    <filter id="ring-shadow" x="-20%" y="-20%" width="140%" height="140%">
      <feDropShadow dx="0" dy="4" stdDeviation="8" flood-color="#000" flood-opacity="0.35"/>
    </filter>
  </defs>

  <!-- Background blocks -->
  <rect class="bg-ocean" x="0" y="0" width="1200" height="1200"/>
  <path class="bg-midnight" d="M655,0 C690,140 750,220 800,260 L1200,260 L1200,1200 L640,1200 Z"/>
  <path class="bg-teal" d="M0,776 L420,360 L840,420 C930,500 990,600 994,700 C998,830 960,930 857,1056 C800,1120 740,1165 689,1200 L0,1200 Z"/>

  <!-- Thin frame -->
  <rect class="frame-line" x="47" y="75" width="1106" height="1080"/>

  <!-- Host portrait -->
  <circle class="portrait-ring" cx="617" cy="317" r="261" filter="url(#ring-shadow)"/>
  <circle cx="617" cy="317" r="240" fill="url(#portrait-fill)" role="img" aria-label="Photo of the two course hosts smiling, one in a black turtleneck with arms crossed and one in a blue denim jacket"/>

  <!-- Course name pill -->
  <rect class="course-pill" x="129" y="567" width="940" height="104" rx="12" ry="12"/>
  <text class="course-name" x="154" y="655" textLength="889" lengthAdjust="spacingAndGlyphs">THE HARVEST LEDGER CIRCLE</text>

  <!-- Headline -->
  <text class="headline" x="127" y="806" textLength="946" lengthAdjust="spacingAndGlyphs">HOW TO LAUNCH</text>
  <text class="headline" x="122" y="930" textLength="955" lengthAdjust="spacingAndGlyphs">A MULTI-MILLION</text>
  <text class="headline" x="120" y="1038" textLength="949" lengthAdjust="spacingAndGlyphs">BUSINESS FROM SCRATCH</text>

  <!-- Call to action -->
  <text class="cta" x="456" y="1097" textLength="274" lengthAdjust="spacingAndGlyphs">SIGN UP TODAY</text>
</svg>
</body>
</html>
```